Vantor Apparel - T-Shirts on Storevia

Hi - I'm creating a new site to sell undershirts. The premise of the undershirt is that it has a U-neck shape so that your white undershirt does not show when you are wearing a button shirt. I want the site to be fun but still look stunning because I want to attract a certain clientele (business professionals with a sense of humor). I'm creating a funny video to post on the site to hopefully get some social media buzz.
I want the design to highlight the product but more importantly the lifestyle of the person who wears it. This is an undershirt so nobody really sees it and that's the point.
Since this is a single product that I want to sell, I want to make sure that the design works with Storevia. Since this is not for theme development, this design must work with an existing theme on Storevia (preferably free but if you must then no more than $75). You can choose the theme to design for.
Products:
* Single vantor undershirt in 4 sizes - S, M, L and XL
* 3 packs or 7 packs (buy 6 get 1 free)
* One-time purchase or subscription (delivery every 3 or 6 months) - I know this will require custom theme development
Attached you will find a very rough idea for the site and this was made before I had considered putting in a video (Brix template). It's going to be tough to catch lightning in a bottle much like Penny Razor Guild but that's what I'm hoping for.
Name of the company is Vantor Apparel. Logo attached. Included .ai file which has some funky colors so please use the light blue color logo similar to the png's attached.
Here is the site for a competitor. There's much to be improved on the site but I include it here because the concept of the undershirt is the same: http://www.mirelgarments.example
Feel free to use stock images that I can purchase on the site that represents a young and cool vibe. I will be taking shots of the shirts for the product page so for now use some generic shirt please.
Updates
Project Deadline Extended
Reason: Please take a look at feedback for other designs. I'm hoping for my mockup to be an inspiration, not just re-skinning the mockup I created. Plus it must be based on a Storevia theme. Use stock images as necessary but keep the budget for purchasing images under $100.
Target Market(s)
Male 30-50

```html
<!DOCTYPE html>
<html lang="en">
<head>
<meta charset="utf-8">
<title>Vantor Apparel – Undershirts for the Modern Man</title>
<link rel="stylesheet" href="https://fonts.googleapis.com/css2?family=Oswald:wght@400;500;600;700&family=Open+Sans:wght@400;600;700&display=swap">
<style>
:root{
  --blue:#27a2dc;
  --blue-dark:#1c87bd;
  --blue-light:#46b3e6;
  --ink:#222222;
  --text:#555555;
  --muted:#8a8a8a;
  --topbar:#1f1d1c;
  --blog-bg:#2f2c2a;
  --footer-bg:#3a3533;
  --bottom-bg:#272321;
  --panel:#f3f3f3;
  --white:#ffffff;
  --rule:#bdbdbd;
}
*{box-sizing:border-box;margin:0;padding:0}
html,body{width:1200px;height:3692px;overflow:hidden}
body{font-family:'Open Sans',Arial,sans-serif;color:var(--text);background:var(--white);position:relative}
.head{font-family:'Oswald','Arial Narrow',sans-serif;text-transform:uppercase;letter-spacing:.5px}
.abs{position:absolute}

/* top bar */
.topbar{position:absolute;left:0;top:0;width:1200px;height:50px;background:var(--topbar);color:#ddd;font-size:13px}
.topbar .welcome{position:absolute;left:14px;top:15px}
.topbar .links{position:absolute;right:40px;top:15px;display:flex;gap:30px}
.topbar .links span{display:flex;align-items:center;gap:8px}

/* header */
.site-header{position:absolute;left:0;top:50px;width:1200px;height:116px;background:var(--white)}
.logo{position:absolute;left:95px;top:33px;font-family:'Oswald',sans-serif;font-weight:500;font-size:40px;color:var(--ink);letter-spacing:.5px}
.nav{position:absolute;right:98px;top:50px;display:flex;gap:34px;align-items:center;font-family:'Oswald',sans-serif;font-weight:600;font-size:14px;color:var(--ink);letter-spacing:.6px}

/* hero */
.hero{position:absolute;left:0;top:166px;width:1200px;height:440px;overflow:hidden}
.hero-photo{position:absolute;inset:0;background:
  radial-gradient(circle at 30% 35%,#c89a7d 0,#7a5a4c 14%,transparent 30%),
  radial-gradient(circle at 78% 80%,#d77b3a 0,transparent 18%),
  radial-gradient(circle at 60% 60%,#9b3b2d 0,transparent 22%),
  linear-gradient(135deg,#1b2236 0%,#2b2030 45%,#3a2418 75%,#16121a 100%)}
.hero-copy{position:absolute;right:112px;top:124px;text-align:center;width:428px}
.hero-kicker{display:inline-block;background:var(--blue);color:var(--white);font-size:29px;font-weight:600;padding:2px 22px;letter-spacing:2px;border:2px solid rgba(255,255,255,.7)}
.hero-title{display:block;margin-top:10px;background:var(--blue);color:var(--white);font-size:58px;font-weight:600;line-height:76px;border:3px solid rgba(255,255,255,.75);letter-spacing:2px}
.hero-cta{display:inline-block;margin-top:6px;background:var(--blue);color:var(--white);font-size:30px;font-weight:700;padding:0 28px;line-height:48px;letter-spacing:2px}

/* section titles */
.section-title{position:absolute;left:50%;transform:translateX(-50%);border:2px solid var(--ink);padding:0 28px;height:50px;line-height:46px;font-family:'Oswald',sans-serif;font-weight:600;font-size:19px;letter-spacing:1px;color:var(--ink);text-transform:uppercase;white-space:nowrap;background:var(--white)}
.section-title.on-dark{border-color:#ddd;color:var(--white);background:transparent}

/* products */
.products-intro{position:absolute;left:190px;top:782px;width:820px;text-align:center;font-size:12.5px;line-height:21px;color:var(--text)}
.read-more{font-family:'Oswald',sans-serif;font-weight:600;font-size:12px;color:var(--ink);text-transform:uppercase;letter-spacing:.3px}
.products-intro .read-more{display:block;margin-top:14px}
.product{position:absolute;top:892px;width:210px;text-align:center}
.product-shot{width:240px;height:220px;margin-left:-15px;background:radial-gradient(ellipse at 50% 50%,#fafafa 0,#ececec 55%,#ffffff 80%)}
.product-name{margin-top:94px;font-family:'Oswald',sans-serif;font-weight:600;font-size:13px;line-height:20px;color:var(--ink);letter-spacing:.5px}
.buy-row{display:flex;height:32px;margin-top:20px;font-family:'Oswald',sans-serif;font-weight:600;font-size:13px;color:var(--white);letter-spacing:.5px}
.buy-row + .buy-row{margin-top:20px}
.buy-row .label{flex:1;background:var(--blue);text-align:left;padding-left:14px;line-height:32px}
.buy-row .price{width:62px;background:var(--blue-dark);line-height:32px}
.shop-now{position:absolute;left:483px;top:1421px;width:234px;height:52px;background:var(--blue);clip-path:polygon(0 0,100% 0,88% 100%,12% 100%);color:var(--white);text-align:center;line-height:52px;font-family:'Oswald',sans-serif;font-weight:700;font-size:22px;letter-spacing:1px}

/* blog */
.blog{position:absolute;left:0;top:1545px;width:1200px;height:741px;background:
  repeating-linear-gradient(45deg,rgba(255,255,255,.015) 0 2px,transparent 2px 5px),var(--blog-bg)}
.post{position:absolute;width:310px}
.post-head{display:flex;align-items:center;gap:16px}
.post-num{width:40px;height:46px;background:var(--blue);color:var(--white);font-family:'Oswald',sans-serif;font-weight:700;font-size:28px;text-align:center;line-height:46px}
.post-title{font-family:'Oswald',sans-serif;font-weight:600;font-size:16px;color:var(--white);letter-spacing:.5px;position:relative;padding-bottom:8px}
.post-title::after{content:"";position:absolute;left:0;bottom:0;width:44px;height:2px;background:#9a9a9a}
.post p{margin-top:10px;font-size:11.5px;line-height:17px;color:#cfcfcf}
.post .read-more{display:block;margin-top:4px;color:var(--white);font-size:11px}

.promo{position:absolute;left:95px;top:618px;width:1007px;height:123px;display:flex}
.promo-photo{position:relative;width:410px;height:123px;background:linear-gradient(90deg,#8d8f91 0%,#b2b3b4 45%,#9c9d9e 100%)}
.promo-photo .figure{position:absolute;left:28px;top:8px;width:90px;height:115px;background:linear-gradient(180deg,#e9e9e9,#d3d3d3)}
.promo-photo .copy{position:absolute;left:168px;top:38px;font-family:'Oswald',sans-serif;font-weight:600;font-size:20px;line-height:22px;color:var(--white)}
.btn-outline{display:inline-block;border:2px solid var(--white);color:var(--white);font-family:'Oswald',sans-serif;font-weight:600;font-size:12px;padding:0 14px;line-height:30px;letter-spacing:.5px}
.promo-photo .btn-outline{position:absolute;left:305px;top:44px;background:rgba(0,0,0,.1)}
.promo-sub{flex:1;margin-left:8px;background:var(--blue);position:relative}
.promo-sub .copy{position:absolute;left:30px;top:36px;font-family:'Oswald',sans-serif;font-weight:600;font-size:22px;line-height:24px;color:var(--white);letter-spacing:.3px}
.promo-sub .btn-outline{position:absolute;right:40px;top:42px}

/* testimonials */
.testimonial{position:absolute;left:95px;top:2474px;width:915px;height:221px;display:flex}
.testimonial-photo{width:288px;height:221px;background:linear-gradient(160deg,#3a3430 0%,#6b5a4e 45%,#2a2522 100%)}
.testimonial-body{flex:1;background:var(--panel);padding:40px 26px}
.testimonial-body h3{font-family:'Oswald',sans-serif;font-weight:600;font-size:16px;color:var(--ink);letter-spacing:.5px}
.testimonial-body h3::after{content:"";display:block;width:48px;height:2px;background:var(--rule);margin-top:10px}
.testimonial-body p{margin-top:18px;font-size:12px;line-height:20px;color:var(--text);width:520px}
.arrows{position:absolute;display:flex;gap:6px}
.arrows span{width:40px;height:46px;background:#dcdcdc;display:flex;align-items:center;justify-content:center}
.rule{position:absolute;left:95px;width:1007px;height:2px;background:var(--rule)}

/* tweets & highlight */
.tweet{position:absolute;left:116px;top:2978px;width:500px}
.tweet h3{font-family:'Oswald',sans-serif;font-weight:600;font-size:15px;color:var(--ink);letter-spacing:.4px}
.tweet p{margin-top:16px;font-size:12px;line-height:20px;color:var(--text);width:500px}
.tweet .by{margin-top:30px;font-size:11px;color:var(--text)}
.tweet .by b{color:var(--ink)}
.video{position:absolute;left:680px;top:2954px;width:340px;height:215px;background:
  radial-gradient(circle at 70% 30%,#8a2a2a 0,transparent 35%),
  radial-gradient(circle at 30% 70%,#4b2a22 0,transparent 40%),
  linear-gradient(135deg,#2a1c1c,#140f12 60%,#3b1e1e)}
.video svg{position:absolute;left:142px;top:79px}

/* footer */
.footer{position:absolute;left:0;top:3240px;width:1200px;height:360px;background:var(--footer-bg)}
.feature{position:absolute;top:0;width:337px;height:360px;text-align:center}
.feature-head{height:100px;background:var(--blue);display:flex;align-items:center;justify-content:center;gap:18px;color:var(--white);font-family:'Oswald',sans-serif;font-weight:600;font-size:17px;letter-spacing:.6px}
.feature.mid .feature-head{background:var(--blue-light)}
.feature .dash{width:44px;height:2px;background:#bdbdbd;margin:24px auto 16px}
.feature p{font-size:11.5px;line-height:18px;color:#d4d4d4;width:260px;margin:0 auto}
.cards{display:flex;justify-content:center;gap:10px;margin-top:14px}
.cards span{width:46px;height:26px;background:#f1f1f1;border-radius:2px}
.feature .btn-outline{margin-top:18px;border-color:#d9d9d9;font-size:11px;line-height:26px;padding:0 22px;border-width:1px}
.feature.first .btn-outline{margin-top:16px}

.bottombar{position:absolute;left:0;top:3600px;width:1200px;height:92px;background:var(--bottom-bg);color:#cfcfcf;font-size:11px}
.bottombar .copy{position:absolute;left:95px;top:40px}
.bottombar .links{position:absolute;left:412px;top:40px;display:flex;gap:18px}
.social{position:absolute;right:98px;top:32px;display:flex;gap:8px}
.social span{width:24px;height:24px;border-radius:2px}
</style>
</head>
<body>

<div class="topbar">
  <span class="welcome">Welcome to our online store! Login or Signup</span>
  <div class="links">
    <span><svg width="11" height="11" viewBox="0 0 12 12"><circle cx="6" cy="6" r="4" fill="none" stroke="#ddd" stroke-width="2"/></svg>Setting</span>
    <span><svg width="11" height="11" viewBox="0 0 12 12"><circle cx="6" cy="3.5" r="2.5" fill="#ddd"/><path d="M1 12a5 5 0 0 1 10 0z" fill="#ddd"/></svg>My Account</span>
    <span><svg width="12" height="11" viewBox="0 0 12 11"><path d="M0 1h2l2 6h6l2-5H3" fill="none" stroke="#ddd" stroke-width="1.4"/><circle cx="5" cy="9.5" r="1" fill="#ddd"/><circle cx="9" cy="9.5" r="1" fill="#ddd"/></svg>Cart: 0 item</span>
  </div>
</div>

<header class="site-header">
  <div class="logo">Vantor Apparel</div>
  <nav class="nav">
    <span>HOME</span><span>CATEGORIES</span><span>ABOUT US</span><span>FAQs</span><span>CONTACT US</span>
    <svg width="13" height="13" viewBox="0 0 14 14"><circle cx="6" cy="6" r="4.5" fill="none" stroke="#222" stroke-width="1.8"/><path d="M9.5 9.5 13 13" stroke="#222" stroke-width="1.8"/></svg>
  </nav>
</header>

<section class="hero">
  <div class="hero-photo" role="img" aria-label="Well-dressed couple on a city balcony at night with blurred lights behind them"></div>
  <div class="hero-copy head">
    <span class="hero-kicker">Undershirts for the</span>
    <span class="hero-title">Modern Man</span>
    <span class="hero-cta">Buy Now</span>
  </div>
</section>

<section class="products">
  <h2 class="section-title" style="top:683px">Our New Products</h2>
  <div class="products-intro">
    Our undershirts sit low at the neck so they stay hidden under any open collar, all day long. Soft cotton, a clean fit and a quiet U-neck for men who like to look sharp
    without showing a white collar line under their shirt. Choose a pack below and pick your size.
    <span class="read-more">Read More</span>
  </div>

  <div class="product" style="left:197px">
    <div class="product-shot" role="img" aria-label="Three folded white U-neck undershirts"></div>
    <div class="product-name">VANTOR UNDERSHIRT<br>3 PACK OF SHIRTS</div>
    <div class="buy-row"><span class="label">BUY NOW</span><span class="price">$15</span></div>
    <div class="buy-row"><span class="label">EVERY 6 MONTH</span><span class="price">$14</span></div>
  </div>
  <div class="product" style="left:495px">
    <div class="product-shot" role="img" aria-label="Seven white U-neck undershirts laid out in a stack"></div>
    <div class="product-name">VANTOR UNDERSHIRT<br>BUY 6 GET 1 FREE/7 SHIRTS</div>
    <div class="buy-row"><span class="label">BUY NOW</span><span class="price">$78</span></div>
    <div class="buy-row"><span class="label">EVERY 6 MONTH</span><span class="price">$72</span></div>
  </div>
  <div class="product" style="left:815px">
    <div class="product-shot" role="img" aria-label="Three folded white U-neck undershirts"></div>
    <div class="product-name">VANTOR UNDERSHIRT<br>3 PACK OF SHIRTS</div>
    <div class="buy-row"><span class="label">BUY NOW</span><span class="price">$15</span></div>
    <div class="buy-row"><span class="label">EVERY 6 MONTH</span><span class="price">$14</span></div>
  </div>

  <div class="shop-now">SHOP NOW</div>
</section>

<section class="blog">
  <h2 class="section-title on-dark" style="top:74px">Lates News From Blog</h2>

  <article class="post" style="left:95px;top:190px">
    <div class="post-head"><span class="post-num">1</span><span class="post-title">AMET VOLUPTATEM</span></div>
    <p>How to wear an open collar at work without a single white line showing through. A short guide for the busy man.</p>
    <span class="read-more">Read More</span>
  </article>
  <article class="post" style="left:445px;top:190px">
    <div class="post-head"><span class="post-num">2</span><span class="post-title">AMET VOLUPTATEM</span></div>
    <p>Five shirts every man should own, and the one layer under them that nobody should ever get to see at all.</p>
    <span class="read-more">Read More</span>
  </article>
  <article class="post" style="left:800px;top:190px">
    <div class="post-head"><span class="post-num">3</span><span class="post-title">AMET VOLUPTATEM</span></div>
    <p>Behind the scenes of our new video shoot, with a few laughs and a lot of very crisp button shirts on set.</p>
    <span class="read-more">Read More</span>
  </article>
  <article class="post" style="left:95px;top:396px">
    <div class="post-head"><span class="post-num">4</span><span class="post-title">AMET VOLUPTATEM</span></div>
    <p>Why a subscription makes sense: fresh shirts arrive every few months, so your drawer never runs thin again.</p>
    <span class="read-more">Read More</span>
  </article>
  <article class="post" style="left:445px;top:396px">
    <div class="post-head"><span class="post-num">5</span><span class="post-title">AMET VOLUPTATEM</span></div>
    <p>Caring for cotton: a simple wash routine that keeps each undershirt soft, bright and in shape for longer.</p>
    <span class="read-more">Read More</span>
  </article>
  <article class="post" style="left:800px;top:396px">
    <div class="post-head"><span class="post-num">6</span><span class="post-title">AMET VOLUPTATEM</span></div>
    <p>Finding your size: how to measure chest and length at home so the fit feels right from the first day.</p>
    <span class="read-more">Read More</span>
  </article>

  <div class="promo">
    <div class="promo-photo">
      <div class="figure" role="img" aria-label="Man in a white t-shirt against a grey concrete wall"></div>
      <div class="copy">BUY 6 GET 1<br>FREE</div>
      <span class="btn-outline">SHOP NOW</span>
    </div>
    <div class="promo-sub">
      <div class="copy">ONE - TIME PURCHASE OR SUBSCRIPTION<br>DELIVERY EVERY 3 OR 6 MONTHS</div>
      <span class="btn-outline">SHOP NOW</span>
    </div>
  </div>
</section>

<section class="reviews">
  <h2 class="section-title" style="top:2360px">What They Says</h2>
  <div class="testimonial">
    <div class="testimonial-photo" role="img" aria-label="Portrait of a young man in a black tuxedo"></div>
    <div class="testimonial-body">
      <h3>JOHN DOE, 25 YO</h3>
      <p>I wear an open collar every day and nobody has seen my undershirt once. Soft, light and it stays put through long meetings and late dinners alike.</p>
    </div>
  </div>
  <div class="arrows" style="left:1010px;top:2474px">
    <span><svg width="12" height="16" viewBox="0 0 12 16"><path d="M9 2 3 8l6 6" fill="none" stroke="#fff" stroke-width="2.5"/></svg></span>
    <span><svg width="12" height="16" viewBox="0 0 12 16"><path d="M3 2l6 6-6 6" fill="none" stroke="#fff" stroke-width="2.5"/></svg></span>
  </div>
  <div class="rule" style="top:2760px"></div>
</section>

<section class="social-block">
  <h2 class="section-title" style="top:2840px;left:257px;transform:none">Recent Tweets</h2>
  <h2 class="section-title" style="top:2840px;left:709px;transform:none">Highlights Product</h2>

  <div class="arrows" style="left:523px;top:2950px">
    <span style="width:40px;height:44px"><svg width="12" height="16" viewBox="0 0 12 16"><path d="M9 2 3 8l6 6" fill="none" stroke="#fff" stroke-width="2.5"/></svg></span>
    <span style="width:40px;height:44px"><svg width="12" height="16" viewBox="0 0 12 16"><path d="M3 2l6 6-6 6" fill="none" stroke="#fff" stroke-width="2.5"/></svg></span>
  </div>

  <div class="tweet">
    <h3>JOHN DOE @ ALVIN BENSON</h3>
    <p>Just tried the new U-neck pack. Open collar all day and not one white line in sight. My shirts finally look the way they should ...</p>
    <div class="by">retweeted by <b>Matt Doe</b></div>
  </div>
  <div class="rule" style="top:3150px;width:525px"></div>

  <div class="video" role="img" aria-label="Video still of a couple embracing in a dark red-lit room">
    <svg width="56" height="56" viewBox="0 0 56 56"><circle cx="28" cy="28" r="27" fill="#fff"/><path d="M23 18v20l16-10z" fill="#2a1c1c"/></svg>
  </div>
</section>

<footer class="footer">
  <div class="feature first" style="left:95px">
    <div class="feature-head">
      <svg width="30" height="28" viewBox="0 0 30 28"><rect x="2" y="6" width="24" height="18" rx="2" fill="#fff"/><rect x="2" y="10" width="24" height="4" fill="#27a2dc"/></svg>
      PAYMENT METHOD
    </div>
    <div class="dash"></div>
    <p>We accept all major cards and<br>pay with one click, safe and fast.</p>
    <div class="cards"><span></span><span></span><span></span><span></span></div>
    <span class="btn-outline">READ MORE</span>
  </div>
  <div class="feature mid" style="left:432px">
    <div class="feature-head">
      <svg width="34" height="24" viewBox="0 0 34 24"><rect x="1" y="3" width="20" height="14" fill="#fff"/><path d="M21 7h7l5 5v5H21z" fill="#fff"/><circle cx="8" cy="19" r="3" fill="#fff" stroke="#46b3e6" stroke-width="1.5"/><circle cx="27" cy="19" r="3" fill="#fff" stroke="#46b3e6" stroke-width="1.5"/></svg>
      FREE SHIPPING
    </div>
    <div class="dash"></div>
    <p>Every order ships free to your<br>door, with no minimum to spend<br>and fast tracked delivery.</p>
    <span class="btn-outline">READ MORE</span>
  </div>
  <div class="feature" style="left:768px">
    <div class="feature-head">
      <svg width="22" height="28" viewBox="0 0 22 28"><path d="M5 12V8a6 6 0 0 1 12 0v4" fill="none" stroke="#fff" stroke-width="3"/><rect x="2" y="12" width="18" height="14" rx="2" fill="#fff"/></svg>
      SECURE SHOPPING
    </div>
    <div class="dash"></div>
    <p>Your details stay private and<br>every checkout is fully secured<br>from start to finish.</p>
    <span class="btn-outline">READ MORE</span>
  </div>
</footer>

<div class="bottombar">
  <span class="copy">© 2016 <b>YOUR COMPANY</b>. ALL RIGHTS RESERVED.</span>
  <div class="links"><span>ABOUT US</span><span>TERM AND USE</span><span>PRIVACY POLICY</span><span>FAQS</span><span>CONTACT US</span></div>
  <div class="social">
    <span style="background:#3b5998"></span>
    <span style="background:#1da1f2"></span>
    <span style="background:#dd4b39"></span>
    <span style="background:#0e76a8"></span>
    <span style="background:#cb2027"></span>
  </div>
</div>

</body>
</html>
```